Business Card (double-sided) and Stationary Design for dental office

1) Business Card Design: We need a business card design for a dental specialty office.
Texts should contain:
The name of our office "Brindle Oaks Orthodontics"
Tagline: "Specialist in Orthodontic and Maxillofacial Orthopedics"
Tag line: "Creating "Tolvering" smiles for Children and Adults"
Doctor name: "Doctor Name"
Office Address:
"123 Street Name
City, State Zip code"
Office email address: office@brindleoaksortho.com
Website: www.brindleoaksortho.com

We will provide the full office address once the design is selected
Theme: beach, paradise, coastal, wave
We would like to have some creativity in design. Some acceptable ideas: front page: logo and office name. Back page: more detail information, and map to office in form of an island. Please see sample from our other location, but you DON'T HAVE TO USE OR COPY THE SAME CONCEPT.

IF POSSIBLE, PLEASE SUBMIT AT LEAST TWO CONCEPTS: ONE WITH THE BACK LOOKING SIMILAR TO WHAT IS IN THE SAMPLE, AND ONE DIFFERENT.

Color: designer to choose. We have different shade of blues and sand color in our office. Please see logo.

2) Please also design a matching set of stationary that compliment the business card and our logo.

Target Market(s)

Dental

Contact Information for Business Card

See descriptions

Font styles to use
Other font styles liked:
• Matching texts in logo

Colors
0054AA
0677BA
7BADD7
CADEEF
E8F1F8
0094D4
00A9DD
6FCCEA
C7EBF8
E9F6FB
00AB8E
00BBA5
67D7C9
C6EFE9
E9F9F6

Requirements
Must have
• Double-sided
Nice to have
• Beach coastal theme
Should not have
• Any shape or drawing of of tooth or teeth. We don’t need these. You don't necessarily have to just cut and paste the logo art and text as a whole, you have the liberty to rearrange the text.

```html
<!DOCTYPE html>
<html lang="en">
<head>
<meta charset="utf-8">
<title>Brindle Oaks Orthodontics – Business Card</title>
<link rel="stylesheet" href="https://fonts.googleapis.com/css2?family=Raleway:wght@400;500;600&family=Arimo&display=swap">
<style>
  :root {
    --teal-deep: #2e88a0;
    --teal-soft: #6cc8bd;
    --ink: #2b2b2b;
    --rule-grey: #cfcfcf;
    --placeholder: #b5b5b5;
    --paper: #ffffff;
    --backdrop: #e4e5e6;
    --sky-top: #5f86e6;
    --sky-mid: #9fc1f2;
    --sea: #7fd3e6;
    --sand: #efe9de;
  }
  * { margin: 0; padding: 0; box-sizing: border-box; }
  html, body { width: 1200px; height: 1200px; overflow: hidden; }
  body { background: var(--backdrop); position: relative; font-family: 'Raleway', sans-serif; }

  .card {
    position: absolute;
    top: 303px;
    height: 593px;
    background: var(--paper);
    overflow: hidden;
    box-shadow: 2px 3px 6px rgba(0,0,0,0.25);
  }
  .card--appointment { left: 200px; width: 370px; }
  .card--contact { left: 599px; width: 364px; text-align: center; }

  /* Appointment side */
  .appointment-title {
    position: absolute; top: 70px; width: 100%;
    text-align: center; font-weight: 500; font-size: 22px;
    color: var(--teal-deep); letter-spacing: 0.2px;
  }
  .appointment-field {
    position: absolute; left: 50px; width: 270px;
    border-bottom: 1.5px solid var(--rule-grey);
    font-family: 'Arimo', sans-serif; font-size: 16px;
    color: var(--placeholder); padding: 0 0 1px 3px;
  }
  .appointment-field--name { top: 140px; }
  .appointment-field--date { top: 189px; }
  .beach-scene { position: absolute; left: 0; top: 0; width: 370px; height: 593px; }

  /* Contact side */
  .brand-dot {
    width: 64px; height: 64px; border-radius: 50%;
    background: var(--teal-deep);
    margin: 74px auto 0;
  }
  .brand-name {
    margin-top: 18px;
    font-weight: 600; font-size: 26px; line-height: 1.1;
    color: var(--teal-deep);
  }
  .person-name { margin-top: 46px; font-weight: 600; font-size: 25px; color: var(--teal-deep); }
  .person-role { font-family: 'Arimo', sans-serif; font-size: 16px; color: var(--ink); margin-top: 2px; }
  .divider { width: 80px; height: 1px; background: var(--teal-soft); margin: 11px auto; }
  .contact-line { font-family: 'Arimo', sans-serif; font-size: 16px; color: var(--ink); line-height: 21px; }
  .specialty { font-weight: 500; font-size: 17px; line-height: 21px; color: var(--teal-deep); }
  .tagline { font-weight: 500; font-size: 17px; line-height: 21px; color: var(--teal-soft); }
</style>
</head>
<body>
  <section class="card card--appointment">
    <svg class="beach-scene" viewBox="0 0 370 593" role="img" aria-label="Photograph of a tropical beach with a palm tree, turquoise sea and blue sky, overlaid with a street map marking the office location">
      <defs>
        <linearGradient id="beachTones" x1="0" y1="0" x2="0" y2="1">
          <stop offset="0" stop-color="var(--sky-top)"/>
          <stop offset="0.45" stop-color="var(--sky-mid)"/>
          <stop offset="0.62" stop-color="var(--sea)"/>
          <stop offset="0.8" stop-color="#c5ecef"/>
          <stop offset="1" stop-color="var(--sand)"/>
        </linearGradient>
      </defs>
      <path d="M0 271 C120 262 280 300 370 390 L370 593 L0 593 Z" fill="url(#beachTones)"/>
    </svg>
    <h2 class="appointment-title">NEXT APPOINTMENT</h2>
    <div class="appointment-field appointment-field--name">Name</div>
    <div class="appointment-field appointment-field--date">Date</div>
  </section>

  <section class="card card--contact">
    <div class="brand-dot"></div>
    <div class="brand-name">Brindle Oaks<br>Orthodontics</div>
    <div class="person-name">Marcus Ellery</div>
    <div class="person-role">Managing Director</div>
    <div class="divider"></div>
    <p class="contact-line">123 Street Name</p>
    <p class="contact-line">City, State Zip code</p>
    <div class="divider"></div>
    <p class="contact-line">office@brindleoaksortho.com</p>
    <p class="contact-line">www.brindleoaksortho.com</p>
    <div class="divider"></div>
    <p class="specialty">Specialist in Orthodontic and<br>Maxillofacial Orthopedics</p>
    <div class="divider"></div>
    <p class="tagline">Creating Tolvering smiles for<br>Children and Adults</p>
  </section>
</body>
</html>
```